Pemberlux: Smart Quotes for Wine Lovers

Hello. I am completing book of quotes for wine lovers. Need the text formatted so that it is easy to read and aesthetically pleasing...modern, clean, smart. Number the pages. The cover is complete. Book is small square. 7.5 by 7.5 inches. If you want to show me first few pages that would be awesome. Thank you!
Updates

I edited the quotes so if you downloaded first ones, please grab these ones instead, thank you! 

Target Market(s)

wine lovers. Urban. Modern.

Industry/Entity Type

Quotes

Requirements
Should not have
• No color. black and white only.

```html
<!DOCTYPE html>
<html lang="en">
<head>
<meta charset="utf-8">
<title>Pemberlux: Smart Quotes for Wine Lovers — Spread 32–33</title>
<link href="https://fonts.googleapis.com/css2?family=Noto+Sans:wght@400;700&display=swap" rel="stylesheet">
<style>
  :root {
    --ink: #000000;
    --paper: #ffffff;
    --caption-grey: #8a8a8a;
    --quote-size: 40px;
  }
  * { margin: 0; padding: 0; box-sizing: border-box; }
  html, body {
    width: 1200px;
    height: 600px;
    overflow: hidden;
    background: var(--paper);
    font-family: "Noto Sans", "DejaVu Sans", Verdana, sans-serif;
  }
  .spread {
    display: flex;
    width: 1200px;
    height: 600px;
  }
  .page {
    position: relative;
    width: 600px;
    height: 600px;
  }
  .page--dark { background: var(--ink); color: var(--paper); }
  .page--light { background: var(--paper); color: var(--ink); }

  .quote {
    position: absolute;
    top: 206px;
    font-size: var(--quote-size);
    line-height: 49px;
    font-weight: 400;
    letter-spacing: 0.01em;
  }
  .page--dark .quote { right: 141px; text-align: right; }
  .page--light .quote { left: 139px; text-align: left; }

  .attribution {
    position: absolute;
    font-size: 13px;
    letter-spacing: 0.08em;
    text-transform: uppercase;
  }
  .page--dark .attribution { top: 419px; right: 141px; }
  .page--light .attribution { top: 371px; left: 139px; }

  .bio {
    position: absolute;
    top: 518px;
    font-size: 7.5px;
    line-height: 10px;
    font-weight: 700;
    white-space: nowrap;
  }
  .page--dark .bio { right: 141px; text-align: right; }
  .page--light .bio { left: 139px; color: var(--caption-grey); }

  .folio {
    position: absolute;
    top: 523px;
    right: 80px;
    font-size: 13px;
  }
</style>
</head>
<body>
  <main class="spread">
    <section class="page page--dark">
      <blockquote class="quote">The connoisseur<br>does not drink<br>wine but tastes<br>its secrets</blockquote>
      <p class="attribution">–Mateo Solaris</p>
      <p class="bio">Mateo Andrés Felipe Solaris i Vergés, painter of the Vallbona<br>coast (1911–1979) Catalan Dreamscape Painter.</p>
    </section>
    <section class="page page--light">
      <blockquote class="quote">Wine is the<br>divine juice of<br>September</blockquote>
      <p class="attribution">–Aurelien</p>
      <p class="bio">Lucien-Henri Baudet, remembered simply as Aurelien.<br>(1702 –1771). French Essayist, Satirist and Letter Writer.</p>
      <p class="folio">33</p>
    </section>
  </main>
</body>
</html>
```